Verlindo Magician

I want the business card for my business to give to people who watch that later I will be employed to show magic here is my website http://www.balsamomagicien.com/I want the interesting design , i am very opened for formal and informal, I watch a lot of design so don't stick to the common shape and form but i hope it can also be produced the thing to write on will be the same as in picture that i will upload , i also will upload the logo for you that so can be easy to useDenis CostilleMagicianMAGICIAN VERLINDO 17 rue des Tilleuls - 25000 BESANÇON contact@verlindoillusions.example tel. 0381 946 157 tel. 0674 219 503

```html
<!DOCTYPE html>
<html lang="fr">
<head>
<meta charset="utf-8">
<title>Verlindo Magician – business card</title>
<link rel="stylesheet" href="https://fonts.googleapis.com/css2?family=Jost:wght@400;500&display=swap">
<style>
  :root {
    --page: #ecebe8;
    --paper: #ffffff;
    --ink: #1d1d1d;
    --grey: #6b6b6b;
    --rule: #b9b9b9;
    --red: #e5252a;
    --band: #111111;
  }
  * { margin: 0; padding: 0; box-sizing: border-box; }
  html, body { width: 1200px; height: 1040px; overflow: hidden; }
  body {
    background: var(--page);
    font-family: "Jost", "Futura", sans-serif;
    position: relative;
  }
  .card {
    position: absolute;
    left: 220px;
    width: 760px;
    height: 430px;
    overflow: hidden;
    box-shadow: 0 6px 18px rgba(0,0,0,.18);
  }
  .card--front { top: 55px; background: var(--paper); }
  .card--back { top: 555px; background: var(--red); }

  /* front */
  .portrait {
    position: absolute;
    border-radius: 46% 46% 18% 18%;
  }
  .card--front .portrait {
    left: 420px; top: 36px; width: 170px; height: 128px;
    background: linear-gradient(160deg, #2a2a2a, #0c0c0c);
  }
  .brand {
    position: absolute;
    left: 600px; top: 118px;
    display: flex; align-items: center; gap: 8px;
    font-size: 24px; font-weight: 400; letter-spacing: 1px;
    color: var(--ink);
  }
  .brand__mark { width: 9px; height: 9px; background: var(--red); }

  .person { position: absolute; left: 44px; top: 210px; }
  .person__name { font-size: 32px; font-weight: 400; color: var(--ink); line-height: 1.1; }
  .person__role { font-size: 21px; color: var(--red); line-height: 1.2; }

  .rule {
    position: absolute; left: 44px; top: 288px;
    width: 680px; height: 1px; background: var(--rule);
  }

  .contact { position: absolute; left: 44px; top: 300px; list-style: none; }
  .contact li {
    display: flex; align-items: center; gap: 12px;
    font-size: 17px; color: var(--grey); line-height: 25px;
  }
  .contact svg { width: 14px; height: 14px; fill: var(--ink); }

  .address {
    position: absolute; right: 36px; top: 302px; text-align: right;
    font-size: 17px; line-height: 24px;
  }
  .address__title { color: var(--red); }
  .address__street { color: var(--grey); }

  .strip {
    position: absolute; left: 0; bottom: 0;
    width: 470px; height: 10px; background: var(--red);
  }
  .band {
    position: absolute; right: 0; bottom: 0;
    width: 320px; height: 46px; background: var(--band);
    clip-path: polygon(14px 0, 100% 0, 100% 100%, 0 100%);
    color: #fff; font-size: 17px; letter-spacing: 2px;
    display: flex; align-items: center; justify-content: flex-end;
    padding-right: 26px;
  }

  /* back */
  .card--back .portrait {
    left: 270px; top: 80px; width: 250px; height: 170px;
    background: linear-gradient(160deg, #1e1e1e, #050505);
  }
  .back__web {
    position: absolute; left: 50px; bottom: 42px;
    color: #fff; font-size: 18px; letter-spacing: 3px;
  }
</style>
</head>
<body>
  <section class="card card--front">
    <div class="portrait" role="img" aria-label="Black and white illustration of the magician holding a playing card"></div>
    <div class="brand"><span class="brand__mark"></span>VERLINDO</div>

    <div class="person">
      <p class="person__name">Marc Ravoulet</p>
      <p class="person__role">Magician</p>
    </div>

    <div class="rule"></div>

    <ul class="contact">
      <li><svg viewBox="0 0 24 24" aria-hidden="true"><path d="M6.6 10.8a15 15 0 0 0 6.6 6.6l2.2-2.2c.3-.3.7-.4 1-.2 1.1.4 2.3.6 3.6.6.6 0 1 .4 1 1V20c0 .6-.4 1-1 1A17 17 0 0 1 3 4c0-.6.4-1 1-1h3.5c.6 0 1 .4 1 1 0 1.3.2 2.5.6 3.6.1.3 0 .7-.2 1z"/></svg>0381 946 157</li>
      <li><svg viewBox="0 0 24 24" aria-hidden="true"><path d="M6.6 10.8a15 15 0 0 0 6.6 6.6l2.2-2.2c.3-.3.7-.4 1-.2 1.1.4 2.3.6 3.6.6.6 0 1 .4 1 1V20c0 .6-.4 1-1 1A17 17 0 0 1 3 4c0-.6.4-1 1-1h3.5c.6 0 1 .4 1 1 0 1.3.2 2.5.6 3.6.1.3 0 .7-.2 1z"/></svg>0674 219 503</li>
      <li><svg viewBox="0 0 24 24" aria-hidden="true"><path d="M2 5h20v14H2zm2 2v.5l8 5 8-5V7z"/></svg>contact@verlindoillusions.example</li>
    </ul>

    <div class="address">
      <p class="address__title">MAGICIAN VERLINDO</p>
      <p class="address__street">17 rue des Tilleuls - 25000 BESANÇON</p>
    </div>

    <div class="strip"></div>
    <div class="band">www.verlindoillusions.example</div>
  </section>

  <section class="card card--back">
    <div class="portrait" role="img" aria-label="Black illustration of the magician holding a playing card"></div>
    <p class="back__web">www.verlindoillusions.example</p>
  </section>
</body>
</html>
```